Medical Practice needs a Letterhead Design

We need a clean, modern letterhead design for our stem cell medical practice.

Industry/Entity Type

Medical

```html
<!DOCTYPE html>
<html lang="en">
<head>
<meta charset="utf-8">
<title>VitaCore Medical Letterhead</title>
<link rel="stylesheet" href="https://fonts.googleapis.com/css2?family=Open+Sans:ital,wght@0,400;0,600;1,400&display=swap">
<style>
  :root {
    --backdrop: #a9a9a9;
    --paper: #ffffff;
    --navy: #143247;
    --lime: #b5c63a;
    --ink: #1e1e1e;
    --contact-blue: #2a5a8c;
    --signature-tone: #e4e6e8;
  }
  * { box-sizing: border-box; margin: 0; padding: 0; }
  html, body { width: 1200px; height: 1000px; overflow: hidden; }
  body {
    background: var(--backdrop);
    font-family: "Open Sans", Arial, sans-serif;
    color: var(--ink);
    position: relative;
  }
  .letterhead {
    position: absolute;
    left: 252px; top: 50px;
    width: 696px; height: 900px;
    background: var(--paper);
    box-shadow: 0 4px 14px rgba(0,0,0,0.25);
    overflow: hidden;
  }
  .brand {
    position: absolute; left: 48px; top: 72px;
    display: flex; align-items: center; gap: 10px;
  }
  .brand-dot { width: 14px; height: 14px; border-radius: 50%; background: var(--lime); }
  .brand-name { font-size: 26px; font-weight: 600; color: var(--navy); letter-spacing: -0.2px; }
  .contact {
    position: absolute; left: 462px; top: 40px;
    padding-left: 14px;
    border-left: 1px solid var(--lime);
    font-size: 9.5px; line-height: 13px;
    color: var(--contact-blue);
  }
  .contact li { list-style: none; display: flex; align-items: center; gap: 6px; }
  .contact svg { width: 8px; height: 8px; fill: var(--contact-blue); }
  .contact .address { margin-top: 3px; font-weight: 600; line-height: 11px; }
  .letter-body {
    position: absolute; left: 56px; top: 160px; width: 570px;
    font-size: 11.5px; line-height: 20px;
    display: flex; flex-direction: column;
  }
  .letter-body .salutation { margin-bottom: 24px; }
  .letter-body .paragraph { margin-bottom: 18px; }
  .sign-off { margin-top: 6px; display: flex; flex-direction: column; gap: 10px; }
  .signature {
    width: 140px; height: 44px;
    background: var(--signature-tone); border-radius: 4px;
  }
  .band-lime {
    position: absolute; left: 0; bottom: 26px;
    width: 330px; height: 22px; background: var(--lime);
  }
  .band-navy {
    position: absolute; right: 0; bottom: 0;
    width: 360px; height: 52px; background: var(--navy);
    border-top-left-radius: 18px;
  }
</style>
</head>
<body>
  <main class="letterhead">
    <header>
      <div class="brand">
        <span class="brand-dot"></span>
        <span class="brand-name">VitaCore Medical</span>
      </div>
      <ul class="contact">
        <li><svg viewBox="0 0 10 10"><path d="M2 0h2l1 3-1.5 1a6 6 0 0 0 2.5 2.5L7 5l3 1v2a2 2 0 0 1-2 2A8 8 0 0 1 0 2a2 2 0 0 1 2-2z"/></svg>(000)555-0142</li>
        <li><svg viewBox="0 0 10 10"><rect x="1" y="3" width="8" height="6"/><rect x="3" y="0" width="4" height="3"/></svg>(000)555-0187</li>
        <li><svg viewBox="0 0 10 10"><path d="M0 2h10v7H0z M0 2l5 4 5-4" /></svg>hello@vitacoremed.com</li>
        <li><svg viewBox="0 0 10 10"><circle cx="5" cy="5" r="5"/></svg>www.vitacoremed.com</li>
        <li class="address">1200 Linden Avenue, Suite 300<br>Brookfield, ST 00000</li>
      </ul>
    </header>

    <section class="letter-body">
      <p class="salutation">Lorem Ipsum is simply</p>
      <p class="paragraph">dummy text of the printing and typesetting industry. Lorem Ipsum has been the industry's standard dummy text ever since the 1500s, when an unknown printer took a galley of type and scrambled it to make a type specimen book. It has survived not only five centuries, but also the leap into electronic typesetting, remaining essentially unchanged. It was popularised in the 1960s with the release of Typeset Press sheets containing Lorem Ipsum passages, and more recently with desktop publishing software like PageForm Studio including versions of Lorem Ipsum.</p>
      <p class="paragraph">It is a long established fact that a reader will be distracted by the readable content of a page when looking at its layout. The point of using Lorem Ipsum is that it has a more-or-less normal distribution of letters, as opposed to using 'Content here, content here', making it look like readable English. Many desktop publishing packages and web page editors now use Lorem Ipsum as their default model text, and a search for 'lorem ipsum' will uncover many web sites still in their infancy. Various versions have evolved over the years, sometimes by accident, sometimes on purpose (injected humour and the like).</p>
      <p class="paragraph">Contrary to popular belief, Lorem Ipsum is not simply random text. It has roots in a piece of classical Latin literature from 45 BC, making it over 2000 years old. Daniel Harwick, a Latin professor at Ashford College in Vermont, looked up one of the more obscure Latin words, consectetur, from a Lorem Ipsum</p>

      <div class="sign-off">
        <p class="closing">Lorem Ipsum</p>
        <div class="signature" role="img" aria-label="Handwritten signature"></div>
        <p class="signer">Lorem Ipsum is a dummy</p>
      </div>
    </section>

    <footer>
      <div class="band-lime"></div>
      <div class="band-navy"></div>
    </footer>
  </main>
</body>
</html>
```